Marcus Delbridge Finance

Need a personal website advertising Equipment Finance,Business Finance,Commercial Finance, Construction Finance, Bridging Finance. Similar websites are www.corvalend.com.au / www.tarmivest.com.au / www.qbr7.com.au /wwwhalvecredit.com.au

Target Market(s)

Business People

Industry/Entity Type

Business

Number of Pages Required

3 page

Font styles to use
Serif
Sans Serif

Requirements
Must have
• All i want is a simple corporate looking website advertising Equipment Finance, Commercial Finance, Construction Finance, Business Finance, Bridging Finance,

```html
<!DOCTYPE html>
<html lang="en">
<head>
<meta charset="utf-8">
<title>Marcus Delbridge Finance</title>
<link rel="stylesheet" href="https://fonts.googleapis.com/css2?family=Open+Sans:wght@400;600;700&family=Lato:wght@400;700&display=swap">
<style>
:root{
  --blue:#2f5aa8;
  --blue-dark:#1d3f96;
  --teal:#188a9a;
  --ink:#111;
  --text:#222;
  --header-bg:#f4f4f4;
  --panel:#e9e9e9;
  --line:#cfcfcf;
  --footer:#000;
  --white:#fff;
}
*{margin:0;padding:0;box-sizing:border-box}
html,body{width:884px;height:1200px;overflow:hidden;background:var(--white)}
body{position:relative;font-family:"Lato",sans-serif;color:var(--text)}
.abs{position:absolute}

/* header */
.site-header{left:0;top:0;width:884px;height:70px;background:var(--header-bg)}
.brand{left:73px;top:12px;display:flex;align-items:center;gap:9px}
.brand-mark{width:46px;height:46px;background:var(--blue)}
.brand-name{font-family:"Open Sans",sans-serif;font-weight:600;font-size:19px;color:var(--ink)}
.main-nav{left:407px;top:33px;display:flex;gap:25px;font-family:"Open Sans",sans-serif;font-weight:600;font-size:10.5px;color:#222}
.main-nav .active{color:var(--blue);position:relative}
.main-nav .active::after{content:"";position:absolute;left:0;right:0;top:36px;height:2px;background:var(--blue)}
.call{left:700px;top:20px;display:flex;align-items:center;gap:8px}
.call-divider{width:1px;height:30px;background:#333}
.call-label{font-family:"Open Sans",sans-serif;font-weight:600;font-size:10.5px;color:var(--blue);line-height:14px}
.call-number{font-family:"Open Sans",sans-serif;font-weight:700;font-size:10.5px;color:#111}

/* hero */
.hero{left:0;top:70px;width:884px;height:380px;background:linear-gradient(180deg,#4f8fd8 0%,#7fb1e3 35%,#c9a57e 62%,#7a4a2a 80%,#2a2a3a 100%)}
.hero-caption{left:157px;top:208px;width:570px;height:94px;background:rgba(60,60,60,.75);display:flex;align-items:center;justify-content:center;text-align:center;font-family:"Open Sans",sans-serif;font-weight:700;font-size:22px;line-height:29px;color:var(--white);text-shadow:0 1px 3px rgba(0,0,0,.6)}
.hero-dots{left:423px;top:362px;display:flex;gap:5px}
.hero-dots span{width:8px;height:8px;border:1px solid #fff}
.hero-dots span:first-child{background:#fff}

/* welcome */
.welcome-title{left:73px;top:496px;font-family:"Open Sans",sans-serif;font-weight:700;font-size:21px;color:var(--ink);white-space:nowrap}
.welcome-title em{font-style:normal;color:var(--blue)}
.rule{height:2px;width:48px;background:var(--blue)}
.welcome-rule{left:73px;top:536px}
.welcome-copy{left:74px;top:557px;width:510px;font-size:10px;line-height:16px;color:#111}
.btn{background:var(--blue);color:var(--white);font-family:"Open Sans",sans-serif;font-weight:600;font-size:10.5px;display:flex;align-items:center;justify-content:center}
.read-more{left:73px;top:657px;width:90px;height:27px}

/* inquiry */
.inquiry{left:611px;top:487px;width:202px;height:206px;background:var(--panel);box-shadow:0 6px 6px -4px rgba(0,0,0,.35)}
.inquiry-title{left:0;top:12px;width:100%;text-align:center;font-family:"Open Sans",sans-serif;font-weight:700;font-size:16px;color:var(--ink)}
.inquiry-title em{font-style:normal;color:var(--blue)}
.field{left:13px;width:176px;height:28px;background:var(--white);border:1px solid var(--line);font-size:8.5px;color:#555;padding:8px 7px}
.submit{left:13px;top:169px;width:176px;height:28px;font-size:12px}

/* services */
.services-band{left:0;top:726px;width:884px;height:135px;background:linear-gradient(120deg,#1d46a8 0%,#2a55b8 45%,#1b6fa6 75%,var(--teal) 100%)}
.services-title{left:0;top:745px;width:884px;text-align:center;font-family:"Open Sans",sans-serif;font-weight:700;font-size:23px;color:var(--white)}
.services-rule{left:418px;top:788px;background:#c7cfe0}
.service{top:821px;width:140px;text-align:center}
.service-icon{width:76px;height:76px;margin:0 auto;background:var(--white);border:2px solid var(--blue);display:flex;align-items:center;justify-content:center}
.service-icon i{display:block;width:40px;height:36px;background:#222}
.service-name{margin-top:12px;font-weight:700;font-size:12.5px;color:#111}

/* footer */
.site-footer{left:0;top:967px;width:884px;height:201px;background:var(--footer)}
.foot-title{top:1000px;font-family:"Open Sans",sans-serif;font-weight:700;font-size:11.5px;color:var(--white)}
.foot-title em{font-style:normal;color:var(--blue)}
.foot-rule{top:1021px;width:25px;height:2px;background:var(--blue)}
.quick-links{left:73px;top:1034px;list-style:none;font-size:9.5px;color:var(--white)}
.quick-links li{height:24px}
.quick-links li::before{content:"•";margin-right:5px}
.quick-links .active{color:var(--blue)}
.contact-list{left:230px;top:1033px;font-size:9.5px;color:var(--white);line-height:13px}
.contact-row{display:flex;gap:8px;margin-bottom:8px}
.contact-row svg{flex:none;margin-top:1px}
.map{left:460px;top:1037px;width:181px;height:94px;border:2px solid #666;background:linear-gradient(135deg,#e8e6dc,#d9d6c8)}
.foot-mark{left:728px;top:1035px;width:62px;height:62px;background:#9a9a9a}
.social{left:712px;top:1114px;display:flex;gap:6px}
.social span{width:19px;height:19px;background:var(--blue)}
.copyright{left:0;top:1168px;width:884px;height:32px;background:var(--blue);color:var(--white);font-size:9.5px;display:flex;align-items:center;justify-content:center}
</style>
</head>
<body>

<header class="site-header abs">
  <div class="brand abs"><span class="brand-mark"></span><span class="brand-name">Marcus Delbridge Finance</span></div>
  <nav class="main-nav abs">
    <span class="active">HOME</span><span>ABOUT US</span><span>SERVICES</span><span>CONTACT US</span>
  </nav>
  <div class="call abs">
    <svg width="26" height="26" viewBox="0 0 24 24"><path fill="#2f5aa8" d="M6.6 10.8a15 15 0 0 0 6.6 6.6l2.2-2.2c.3-.3.7-.4 1-.2 1.1.4 2.3.6 3.6.6.6 0 1 .4 1 1V20c0 .6-.4 1-1 1A17 17 0 0 1 3 4c0-.6.4-1 1-1h3.5c.6 0 1 .4 1 1 0 1.3.2 2.5.6 3.6.1.3 0 .7-.2 1z"/></svg>
    <span class="call-divider"></span>
    <div><div class="call-label">CALL US</div><div class="call-number">(123)-555-0147</div></div>
  </div>
</header>

<section class="hero abs" role="img" aria-label="City skyline of glass towers at sunset with light trails on a highway"></section>
<div class="hero-caption abs">We Are A Business Firm Which Provides Finance<br>To Small&nbsp; Business Throught UK</div>
<div class="hero-dots abs"><span></span><span></span><span></span></div>

<h1 class="welcome-title abs">WELCOME TO <em>MARCUS DELBRIDGE</em> FINANCE</h1>
<div class="rule welcome-rule abs"></div>
<p class="welcome-copy abs">Lorem ipsum dolor sit amet, consectetuer adipiscing elit, sed diam nonummy nibh euismod tincidunt ut laoreet dolore magna aliquam erat volutpat. Ut wisi enim ad minim veniam, quis nostrud exerci tation ullamcorper suscipit lobortis nisl ut aliquip ex ea commodo consequat. Duis autem vel eum iriure dolor in hendrerit in vulputate velit esse molestie consequat, vel illum dolore eu feugiat nulla facilisis at vero eros et accumsan et iusto odio dignissim qui blandit praesent luptatum zzril delenit augue duis dolore te feugait nulla facilisi.</p>
<div class="btn read-more abs">READ MORE</div>

<aside class="inquiry abs">
  <h2 class="inquiry-title abs">QUICK <em>INQUIRY</em></h2>
  <div class="field abs" style="top:42px">Name</div>
  <div class="field abs" style="top:75px">Email</div>
  <div class="field abs" style="top:108px;height:52px">Message</div>
  <div class="btn submit abs">SUBMIT</div>
</aside>

<section>
  <div class="services-band abs"></div>
  <h2 class="services-title abs">OUR SERVICES</h2>
  <div class="rule services-rule abs"></div>
  <div class="service abs" style="left:58px"><div class="service-icon"><i role="img" aria-label="Excavator icon"></i></div><div class="service-name">Equipment Finance</div></div>
  <div class="service abs" style="left:214px"><div class="service-icon"><i role="img" aria-label="Hand holding money icon"></i></div><div class="service-name">Business Finance</div></div>
  <div class="service abs" style="left:373px"><div class="service-icon"><i role="img" aria-label="Office building icon"></i></div><div class="service-name">Commercial Finance</div></div>
  <div class="service abs" style="left:528px"><div class="service-icon"><i role="img" aria-label="Crane and building icon"></i></div><div class="service-name">Construction Finance</div></div>
  <div class="service abs" style="left:684px"><div class="service-icon"><i role="img" aria-label="Bridge icon"></i></div><div class="service-name">Bridging Finance</div></div>
</section>

<footer>
  <div class="site-footer abs"></div>
  <h3 class="foot-title abs" style="left:73px">QUICK <em>LINKS</em></h3>
  <div class="foot-rule abs" style="left:73px"></div>
  <ul class="quick-links abs">
    <li class="active">HOME</li><li>ABOUT US</li><li>SERVICES</li><li>CONTACT US</li>
  </ul>

  <h3 class="foot-title abs" style="left:229px">CONTACT <em>DETAILS</em></h3>
  <div class="foot-rule abs" style="left:229px"></div>
  <div class="contact-list abs">
    <div class="contact-row"><svg width="9" height="12" viewBox="0 0 10 14"><path fill="#2f5aa8" d="M5 0a5 5 0 0 0-5 5c0 4 5 9 5 9s5-5 5-9a5 5 0 0 0-5-5zm0 7a2 2 0 1 1 0-4 2 2 0 0 1 0 4z"/></svg><div><b>Marcus Delbridge Finance</b><br>Sed ut perspiciatis unde omnis<br>iste natus errorluptatem</div></div>
    <div class="contact-row"><svg width="9" height="10" viewBox="0 0 24 24"><path fill="#2f5aa8" d="M6.6 10.8a15 15 0 0 0 6.6 6.6l2.2-2.2c.3-.3.7-.4 1-.2 1.1.4 2.3.6 3.6.6.6 0 1 .4 1 1V20c0 .6-.4 1-1 1A17 17 0 0 1 3 4c0-.6.4-1 1-1h3.5c.6 0 1 .4 1 1 0 1.3.2 2.5.6 3.6.1.3 0 .7-.2 1z"/></svg><div>0123 555 014</div></div>
    <div class="contact-row"><svg width="9" height="9" viewBox="0 0 10 8"><rect width="10" height="8" fill="#2f5aa8"/><path d="M0 0l5 4 5-4" stroke="#000" fill="none"/></svg><div>info@delbridgefinance.com</div></div>
  </div>

  <h3 class="foot-title abs" style="left:458px">LOCATION <em>MAP</em></h3>
  <div class="foot-rule abs" style="left:458px"></div>
  <div class="map abs" role="img" aria-label="Street map of the office location"></div>

  <div class="foot-mark abs"></div>
  <div class="social abs"><span></span><span></span><span></span><span></span></div>

  <div class="copyright abs">Copyright © 2017 Marcus Delbridge Finance. All Rights Reserved</div>
</footer>

</body>
</html>
```